MBR - Stationery Design Project

We need stationery based on our logo.

Company info :
Cabinet Voisard & Associés
Société à responsabilité limitée au capital de 200.000 FCFP
RCS Papeete 27586K - Numéro tahiti K73962
Centre d’affaires OPALE - Rue Gaston Perrin
BP 61384 MAHU POTE - 98752 Papeete
Tahiti - Polynésie française
Tél : +689 40 73 16 48
Fax : +689 40 39 64 91

Industry/Entity Type

It Company

Font styles to use
Sans Serif

```html
<!DOCTYPE html>
<html lang="fr">
<head>
<meta charset="utf-8">
<title>MBR – Papeterie</title>
<link rel="stylesheet" href="https://fonts.googleapis.com/css2?family=Questrial&family=Arimo:wght@400;700&display=swap">
<style>
  :root {
    --navy: #1c3a5e;
    --slate: #8a9a9c;
    --ink-grey: #6f6f6f;
    --soft-grey: #a9a9a9;
    --rule: #9a9a9a;
    --paper: #ffffff;
    --backdrop: #e9e9e9;
  }
  * { margin: 0; padding: 0; box-sizing: border-box; }
  html, body { width: 1200px; height: 815px; overflow: hidden; }
  body {
    position: relative;
    background: var(--backdrop);
    font-family: "Questrial", sans-serif;
  }
  .sheet {
    position: absolute;
    top: 70px;
    width: 483px;
    height: 685px;
    background: var(--paper);
  }
  .sheet--letterhead { left: 80px; }
  .sheet--fax { left: 638px; }

  .brand { position: absolute; left: 38px; top: 30px; }
  .brand__name {
    font-size: 56px;
    line-height: 48px;
    color: var(--navy);
    letter-spacing: -1px;
  }
  .brand__company {
    font-size: 11px;
    color: var(--navy);
    margin-top: 2px;
    white-space: nowrap;
  }
  .brand__services {
    font-size: 5px;
    color: var(--slate);
    margin-left: 22px;
    margin-top: 1px;
  }

  .fax-title {
    position: absolute;
    right: 40px;
    top: 26px;
    font-family: "Arimo", sans-serif;
    font-size: 54px;
    color: var(--navy);
    letter-spacing: 1px;
  }

  .fax-details {
    position: absolute;
    left: 39px;
    top: 148px;
    width: 406px;
    border-collapse: collapse;
    font-family: "Arimo", sans-serif;
    font-size: 7px;
    font-weight: 700;
    color: var(--ink-grey);
  }
  .fax-details td {
    border: 1px solid var(--rule);
    height: 13.5px;
    padding: 0 4px;
  }
  .fax-details .label { width: 43px; }
  .fax-details .value { width: 158px; }
  .fax-details .label--right { width: 44px; }

  .fax-status {
    position: absolute;
    left: 39px;
    top: 230px;
    width: 406px;
    height: 15px;
    display: flex;
    border: 1px solid var(--rule);
    background: #ececec;
    font-family: "Arimo", sans-serif;
    font-size: 7px;
    font-weight: 700;
    color: var(--ink-grey);
  }
  .fax-status__item {
    flex: 1;
    display: flex;
    align-items: center;
    justify-content: center;
    gap: 4px;
    border-right: 1px solid var(--rule);
  }
  .fax-status__item:last-child { border-right: none; }
  .checkbox { width: 5px; height: 5px; border: 1px solid var(--ink-grey); }

  .fax-comments {
    position: absolute;
    left: 39px;
    top: 245px;
    width: 406px;
    height: 350px;
    border: 1px solid var(--rule);
    border-top: none;
    font-family: "Arimo", sans-serif;
    font-size: 7px;
    color: var(--ink-grey);
    text-align: center;
    padding-top: 10px;
  }

  .footer-address {
    position: absolute;
    left: 38px;
    top: 635px;
    font-size: 6.6px;
    line-height: 9px;
    color: #4a4a4a;
  }
  .footer-address strong { color: var(--navy); font-weight: 400; }
  .footer-legal {
    position: absolute;
    right: 38px;
    top: 644px;
    font-size: 6.2px;
    line-height: 9px;
    color: var(--soft-grey);
    text-align: right;
  }
  .footer-bands { position: absolute; left: 0; bottom: 0; width: 100%; height: 12px; }
</style>
</head>
<body>

<section class="sheet sheet--letterhead">
  <div class="brand">
    <div class="brand__name">MBR</div>
    <div class="brand__company">Cabinet Voisard &amp; Associés</div>
    <div class="brand__services">Expertise-comptable · Audit · Conseil</div>
  </div>
  <address class="footer-address" style="font-style:normal">
    Centre d’affaires OPALE - Rue Gaston Perrin, BP 61384<br>
    MAHU POTE - 98752 Papeete, Tahiti - Polynésie française<br>
    <strong>Tél:</strong> +689 40 73 16 48 · <strong>Fax:</strong> +689 40 39 64 91
  </address>
  <p class="footer-legal">
    Société à responsabilité limitée au capital de 200.000 FCFP<br>
    RCS Papeete 27586K - Numéro tahiti K73962
  </p>
  <svg class="footer-bands" viewBox="0 0 483 12" preserveAspectRatio="none" aria-hidden="true">
    <rect x="0" y="0" width="239" height="12" fill="var(--navy)"/>
    <rect x="242" y="0" width="241" height="12" fill="var(--slate)"/>
  </svg>
</section>

<section class="sheet sheet--fax">
  <div class="brand">
    <div class="brand__name">MBR</div>
    <div class="brand__company">Cabinet Voisard &amp; Associés</div>
    <div class="brand__services">Expertise-comptable · Audit · Conseil</div>
  </div>
  <h1 class="fax-title">FAX</h1>

  <table class="fax-details">
    <tr><td class="label">To:</td><td class="value"></td><td class="label label--right">From:</td><td></td></tr>
    <tr><td class="label">Fax:</td><td class="value"></td><td class="label label--right">Pages:</td><td></td></tr>
    <tr><td class="label">Phone:</td><td class="value"></td><td class="label label--right">Date:</td><td></td></tr>
    <tr><td class="label">Re:</td><td class="value"></td><td class="label label--right">CC:</td><td></td></tr>
  </table>

  <div class="fax-status">
    <div class="fax-status__item"><span class="checkbox"></span>Urgent</div>
    <div class="fax-status__item"><span class="checkbox"></span>For Review</div>
    <div class="fax-status__item"><span class="checkbox"></span>Please Comment</div>
    <div class="fax-status__item"><span class="checkbox"></span>Please Reply</div>
    <div class="fax-status__item"><span class="checkbox"></span>Please Recycle</div>
  </div>
  <div class="fax-comments">COMMENTS:</div>

  <address class="footer-address" style="font-style:normal">
    Centre d’affaires OPALE - Rue Gaston Perrin, BP 61384<br>
    MAHU POTE - 98752 Papeete, Tahiti - Polynésie française<br>
    <strong>Tél:</strong> +689 40 73 16 48 · <strong>Fax:</strong> +689 40 39 64 91
  </address>
  <p class="footer-legal">
    Société à responsabilité limitée au capital de 200.000 FCFP<br>
    RCS Papeete 27586K - Numéro tahiti K73962
  </p>
  <svg class="footer-bands" viewBox="0 0 483 12" preserveAspectRatio="none" aria-hidden="true">
    <rect x="0" y="0" width="239" height="12" fill="var(--navy)"/>
    <rect x="242" y="0" width="241" height="12" fill="var(--slate)"/>
  </svg>
</section>

</body>
</html>
```